Website for enterprise software start-up

We need a new Wordpress website. We are an early stage start-up focused on mobile video technology for cellular operators. The audience is strategy, marketing and customer acquisition execs from the operators.

The purpose of the site is to act as a sales brochure and capture leads. A demo app can be downloaded from the current site, want to put that behind a contact form.

Current website is at www.velmora.tv. Similar number of pages. Looking for a clean design template, with minimal customization. Blog will remain as is.

Want to be able to modify the copy via Wordpress. Reference designs I like: quandrix.com, briskfold7metrics.com

Target Market(s)

Mobile operators and MVNOs in the US and Asia Pacific regions

Industry/Entity Type

Business Software

Coding

Coded - Design and coding required

Number of Pages Required

4 page

Font styles to use
Sans Serif

Colors
f78f20

Requirements
Must have
• Form for downloading sample apps.
• Landing page with image, Product, Blog, About, Contact
• Team page

```html
<!DOCTYPE html>
<html lang="en">
<head>
<meta charset="utf-8">
<title>Velmora Media</title>
<link href="https://fonts.googleapis.com/css2?family=Lato:wght@400;700;900&display=swap" rel="stylesheet">
<style>
:root{
  --orange:#e2731a;
  --ink:#222222;
  --text:#3a3a3a;
  --muted:#777777;
  --light:#f2f2f2;
  --band:#e6e6e6;
  --dark:#333333;
  --darker:#1f1f1f;
  --white:#ffffff;
}
*{margin:0;padding:0;box-sizing:border-box}
html,body{width:1200px;height:3719px;overflow:hidden}
body{position:relative;font-family:'Lato',sans-serif;color:var(--text);background:var(--white)}
.abs{position:absolute}
section,header,footer{position:absolute;left:0;width:1200px}

/* header */
.site-header{top:0;height:82px;background:var(--white)}
.brand{left:82px;top:22px;display:flex;align-items:center;gap:12px}
.brand-dot{width:30px;height:30px;border-radius:50%;background:var(--orange)}
.brand-name{font-weight:700;font-size:30px;color:var(--ink);line-height:1}
.nav{top:36px;left:0;width:1200px;font-size:15px;font-weight:700;color:var(--ink)}
.nav a{position:absolute;text-decoration:none;color:inherit;text-transform:uppercase}
.nav a.active{color:var(--orange)}
.nav a.active::after{content:"";position:absolute;left:50%;top:26px;margin-left:-8px;border:8px solid transparent;border-top:10px solid var(--orange)}

/* hero */
.hero{top:82px;height:558px;color:var(--white);text-align:center}
.hero-photo{position:absolute;inset:0;background:radial-gradient(ellipse at 55% 45%,#8a8e96 0%,#55595f 40%,#2c2f34 100%)}
.hero h1{position:absolute;top:152px;width:100%;font-size:42px;font-weight:700}
.hero p{position:absolute;top:232px;left:280px;width:640px;font-size:21px;line-height:31px}
.btn{display:inline-block;background:var(--orange);color:var(--white);font-size:24px;text-decoration:none}
.hero .btn{position:absolute;left:478px;top:332px;width:243px;height:52px;line-height:52px}
.dots{position:absolute;top:406px;left:566px;display:flex;gap:6px}
.dots span{width:13px;height:13px;border-radius:50%;background:var(--white)}
.dots span:first-child{background:transparent;border:2px solid var(--white)}

/* section titles */
.sec-title{position:absolute;width:100%;text-align:center;font-size:34px;font-weight:700;color:var(--ink)}
.rule{position:absolute;left:550px;width:100px;height:3px;background:#cfcfcf}

/* push */
.push{top:640px;height:669px;background:var(--light)}
.feature{position:absolute;left:82px;display:flex;align-items:center;gap:20px;font-size:17px;line-height:26px;color:var(--text)}
.icon-circle{width:80px;height:80px;border-radius:50%;background:var(--white);border:2px solid #e3e3e3;display:flex;align-items:center;justify-content:center;flex:none}
.device{position:absolute;border-radius:34px}

/* native */
.native{top:1309px;height:667px;background:var(--orange);color:var(--white)}
.native .sec-title{color:var(--white)}
.native .rule{background:#f4b27a}
.native-item{position:absolute;right:82px;display:flex;align-items:center;gap:20px;font-size:17px;line-height:26px;text-align:right;justify-content:flex-end;width:900px}
.native-item .icon-circle{background:var(--white);border:none}

/* team */
.team{top:1976px;height:577px;background:var(--light)}
.quote{position:absolute;width:478px;padding:26px 24px;font-size:17px;font-weight:700;line-height:30px;color:var(--white);border-radius:8px}
.quote::after{content:"";position:absolute;bottom:-26px;border:14px solid transparent}
.quote-dark{background:var(--dark)}
.quote-dark::after{left:140px;border-top-color:var(--dark)}
.quote-orange{background:var(--orange)}
.quote-orange::after{left:130px;border-top-color:var(--orange)}
.portrait{position:absolute;width:156px;height:111px;background:linear-gradient(135deg,#b9b2a8,#7d8590);border:5px solid var(--white);box-shadow:0 1px 4px rgba(0,0,0,.2)}
.person{position:absolute}
.person b{display:block;font-size:24px;color:var(--ink)}
.person span{font-size:16px;color:var(--muted)}
.arrow{position:absolute;width:40px;height:40px;border-radius:50%;background:var(--white);border:1px solid #d6d6d6}

/* clients */
.clients{top:2553px;height:310px;background:var(--white)}
.client{position:absolute;top:144px;height:117px;border:2px solid #e2e2e2;display:flex;align-items:center;justify-content:center;font-weight:700;font-size:22px;color:#8a8a8a;text-align:center}

/* partner */
.partner{top:2863px;height:97px;background:var(--band)}
.partner-badge{position:absolute;left:161px;top:14px;width:82px;height:68px;border-radius:10px;background:#2f6fd1}
.partner p{position:absolute;left:342px;top:35px;font-size:21px;color:var(--ink)}
.partner p a{color:var(--orange);font-weight:700;text-decoration:none}

/* download */
.download{top:2960px;height:230px;color:var(--white);text-align:center}
.download-photo{position:absolute;inset:0;background:linear-gradient(90deg,#3e4a57 0%,#7b8592 50%,#4b5663 100%)}
.download h2{position:absolute;top:40px;width:100%;font-size:28px;font-weight:400}
.store{position:absolute;top:94px;height:50px;background:#111;border:1px solid #888;border-radius:6px;font-size:16px;font-weight:700;display:flex;align-items:center;justify-content:center;gap:8px}
.store i{width:16px;height:16px;background:var(--white);display:block}

/* contact */
.contact{top:3190px;height:467px;background:var(--dark)}
.mail-badge{position:absolute;left:553px;top:-47px;width:94px;height:94px;border-radius:50%;background:var(--orange);display:flex;align-items:center;justify-content:center}
.field{position:absolute;background:var(--white);font-size:15px;font-style:italic;color:#555;padding:20px 18px}
.submit{position:absolute;left:102px;top:395px;width:124px;height:47px;background:var(--orange);color:var(--white);font-size:19px;font-weight:700;display:flex;align-items:center;justify-content:center}

/* footer */
.site-footer{top:3657px;height:62px;background:var(--darker);color:#cfcfcf;font-size:13px}
.site-footer p{position:absolute;left:82px;top:23px}
.social{position:absolute;left:984px;top:17px;display:flex;gap:10px}
.social span{width:26px;height:26px;border-radius:50%;display:block;background:#555}
</style>
</head>
<body>

<header class="site-header">
  <div class="brand abs">
    <div class="brand-dot"></div>
    <div class="brand-name">Velmora Media</div>
  </div>
  <nav class="nav abs">
    <a class="active" style="left:488px">Home</a>
    <a style="left:578px">Product</a>
    <a style="left:694px">Blog</a>
    <a style="left:776px">About Us</a>
    <a style="left:895px">Our Team</a>
    <a style="left:1016px">Contact Us</a>
  </nav>
</header>

<section class="hero">
  <div class="hero-photo" role="img" aria-label="Photo of hands holding a smartphone"></div>
  <h1>High Quality Mobile Engagement</h1>
  <p>We Engage Mobile Audiences With The Right Video Content At The Perfect Moment</p>
  <a class="btn">Get Sample Apps</a>
  <div class="dots"><span></span><span></span><span></span><span></span></div>
</section>

<section class="push">
  <h2 class="sec-title" style="top:36px">Push Video Notifications</h2>
  <div class="rule" style="top:96px"></div>

  <div class="feature" style="top:150px">
    <div class="icon-circle"><svg width="40" height="40" viewBox="0 0 40 40"><path d="M20 6c-6 0-9 5-9 10v8l-3 4h24l-3-4v-8c0-5-3-10-9-10z" fill="#e2731a"/><circle cx="20" cy="32" r="3" fill="#e2731a"/></svg></div>
    <span>Reach Your Mobile Audience With Beautiful HD Thumbnails And<br>In-notification Videos</span>
  </div>
  <div class="feature" style="top:250px">
    <div class="icon-circle"><svg width="40" height="40" viewBox="0 0 40 40"><rect x="6" y="8" width="28" height="24" fill="#e2731a"/><path d="M17 14l9 6-9 6z" fill="#fff"/></svg></div>
    <span>Instant Video Playback, Zero Buffering, Guaranteed Flawless Playback -<br>Even When Offline</span>
  </div>
  <div class="feature" style="top:349px">
    <div class="icon-circle"><svg width="40" height="40" viewBox="0 0 40 40"><rect x="6" y="6" width="22" height="14" fill="#e2731a"/><path d="M16 14h5v10h6l3 10H16z" fill="#e2731a"/></svg></div>
    <span>Content Is Personalised Based On Viewer Interests And Mobile Viewing<br>Habits</span>
  </div>
  <div class="feature" style="top:441px">
    <div class="icon-circle"><svg width="40" height="40" viewBox="0 0 40 40"><rect x="8" y="12" width="24" height="6" fill="#e2731a"/><rect x="8" y="20" width="24" height="6" fill="#e2731a"/><rect x="8" y="28" width="24" height="6" fill="#e2731a"/></svg></div>
    <span>Monetize With Beautiful HD Preroll Or Interstitial Ads</span>
  </div>
  <div class="feature" style="top:540px">
    <div class="icon-circle"><svg width="40" height="40" viewBox="0 0 40 40"><circle cx="20" cy="20" r="14" fill="none" stroke="#e2731a" stroke-width="3"/><path d="M20 11v10h7" fill="none" stroke="#e2731a" stroke-width="3"/></svg></div>
    <span>Easily Added To Your Existing Apps Within One Hour</span>
  </div>

  <div class="device" style="left:843px;top:148px;width:216px;height:459px;background:linear-gradient(180deg,#f5f5f5,#dcdcdc);border:2px solid #cfcfcf" role="img" aria-label="Smartphone showing a lock screen video notification"></div>
</section>

<section class="native">
  <h2 class="sec-title" style="top:42px">Native Push Video</h2>
  <div class="rule" style="top:100px"></div>

  <div class="device" style="left:82px;top:166px;width:200px;height:420px;background:linear-gradient(180deg,#f4f4f4,#cfcfcf)" role="img" aria-label="White smartphone showing a video trailer app"></div>
  <div class="device" style="left:190px;top:166px;width:199px;height:429px;background:linear-gradient(180deg,#3b3b3b,#1a1a1a);border:4px solid #2aa0e0" role="img" aria-label="Blue smartphone showing a video trailer app"></div>

  <div class="native-item" style="top:146px">
    <span>Guarantee Your Audience Never Gets Frustrated With A Poor Quality<br>Mobile Video Streaming Experience</span>
    <div class="icon-circle"><svg width="40" height="40" viewBox="0 0 40 40"><circle cx="20" cy="16" r="10" fill="#333"/><path d="M14 24l-3 12 9-5 9 5-3-12z" fill="#333"/></svg></div>
  </div>
  <div class="native-item" style="top:243px">
    <span>Instant Video Playback, Zero Buffering, HD Quality Guranteed - Even<br>When Offline</span>
    <div class="icon-circle"><svg width="44" height="44" viewBox="0 0 44 44"><path d="M22 2l20 20-20 20L2 22z" fill="#333"/><text x="22" y="27" text-anchor="middle" font-family="Lato,sans-serif" font-weight="900" font-size="13" fill="#fff">HD</text></svg></div>
  </div>
  <div class="native-item" style="top:342px">
    <span>Content Is Personalised Based On Viewer Interests And Mobile Viewing<br>Habits</span>
    <div class="icon-circle"><svg width="44" height="44" viewBox="0 0 44 44"><path d="M4 22c6-10 30-10 36 0-6 10-30 10-36 0z" fill="#333"/><circle cx="22" cy="22" r="6" fill="#fff"/></svg></div>
  </div>
  <div class="native-item" style="top:438px">
    <span>Monetize With Beautiful HD Preroll Or Interstitial Ads</span>
    <div class="icon-circle"><svg width="40" height="40" viewBox="0 0 40 40"><rect x="5" y="7" width="30" height="26" fill="none" stroke="#333" stroke-width="3"/><path d="M5 13h30" stroke="#333" stroke-width="3"/><rect x="20" y="19" width="11" height="9" fill="#333"/></svg></div>
  </div>
  <div class="native-item" style="top:538px">
    <span>Use Your Existing Content Management And Hosting Systems</span>
    <div class="icon-circle"><svg width="40" height="40" viewBox="0 0 40 40"><rect x="8" y="6" width="24" height="8" fill="#333"/><rect x="8" y="16" width="24" height="8" fill="#333"/><rect x="8" y="26" width="24" height="8" fill="#333"/></svg></div>
  </div>
</section>

<section class="team">
  <h2 class="sec-title" style="top:40px">Our Team</h2>
  <div class="rule" style="top:98px"></div>

  <div class="arrow" style="left:20px;top:260px"><svg width="40" height="40" viewBox="0 0 40 40"><path d="M23 13l-7 7 7 7" fill="none" stroke="#999" stroke-width="2"/></svg></div>
  <div class="arrow" style="left:1135px;top:260px"><svg width="40" height="40" viewBox="0 0 40 40"><path d="M17 13l7 7-7 7" fill="none" stroke="#999" stroke-width="2"/></svg></div>

  <div class="quote quote-dark" style="left:102px;top:154px">Lorem ipsum dolor sit amet, onsectietuer icing eliterei sed diam nonummy nibh euismod erere tincideuntr ut laoreet dolore gna werwerweere roererere aliquama aerere era</div>
  <div class="portrait" style="left:161px;top:374px" role="img" aria-label="Portrait of Marcus"></div>
  <div class="person" style="left:330px;top:414px"><b>Marcus</b><span>CEO, Velmora Media</span></div>

  <div class="quote quote-orange" style="left:619px;top:201px">Lorem ipsum dolor sit amet, onsectietuer icing eliterei sed diam nonummy nibh euismod erere tincideuntr ut laoreet dolore gna werwerweere roererere aliquama aerere era</div>
  <div class="portrait" style="left:640px;top:419px" role="img" aria-label="Portrait of Glen"></div>
  <div class="person" style="left:810px;top:461px"><b>Glen</b><span>Vice President, Velmora Media</span></div>
</section>

<section class="clients">
  <h2 class="sec-title" style="top:36px">Our Clients</h2>
  <div class="rule" style="top:96px"></div>
  <div class="client" style="left:82px;width:225px">Northgate TV</div>
  <div class="client" style="left:325px;width:181px">Streamlane</div>
  <div class="client" style="left:523px;width:181px">Harbor Hoops</div>
  <div class="client" style="left:721px;width:162px">Northgate TV</div>
  <div class="client" style="left:900px;width:216px">Keystone Music</div>
</section>

<section class="partner">
  <div class="partner-badge"></div>
  <p><a>Contact Us</a> For Details Of How To Become A Certified Developer Partner.</p>
</section>

<section class="download">
  <div class="download-photo" role="img" aria-label="Photo of a person using a smartphone"></div>
  <h2>Fill Up The Form To Get Link For Downloading Sample Apps</h2>
  <div class="store" style="left:407px;width:156px"><i></i>AppVault</div>
  <div class="store" style="left:602px;width:159px"><i></i>PlayDepot</div>
</section>

<section class="contact">
  <div class="mail-badge"><svg width="50" height="36" viewBox="0 0 50 36"><rect x="2" y="2" width="46" height="32" fill="#fff"/><path d="M2 2l23 18L48 2" fill="none" stroke="#e2731a" stroke-width="3"/></svg></div>
  <div class="field" style="left:102px;top:80px;width:486px;height:67px">Your Name</div>
  <div class="field" style="left:612px;top:80px;width:486px;height:67px">Your Email</div>
  <div class="field" style="left:102px;top:162px;width:996px;height:69px">Subject</div>
  <div class="field" style="left:102px;top:241px;width:996px;height:139px">Message</div>
  <div class="submit">Submit</div>
</section>

<footer class="site-footer">
  <p>Copyright © 2016 Velmora Media. All Rights Reserved.</p>
  <div class="social">
    <span aria-label="Friendlink"></span>
    <span aria-label="Chirpnet"></span>
    <span aria-label="Circlewave"></span>
    <span aria-label="Careerweb"></span>
  </div>
</footer>

</body>
</html>
```